Business card for a Exhibition booth fabrication company

Hi. My company would like to change our corporate name card. We are an events and Exhibition stand builder company. We would like our corporate name card to resonate what we do. I need someone to create something unique that relates to the industry that I am in. The graphic designer should be creative to incorporate the elements of my industry and try to blend in well in the design of the card. Our aim is to ensure that we are unique and our card can look different from our competitors.
Updates

Target Market(s)

Marketing and events manager from all companies

Contact Information for Business Card

The business card should have the following details:
Name
Job Title
Email
Website

Colors

Designer to choose colors to be used in the design.

Requirements
Must have
• The card must be look something that is relevant to the service that I am providing. My website is: www.velmora-buildworks.com
• You can see my website to get more information on what service that I am doing
Nice to have
• On the back of my card, I would like to have a globe image with the incorporation of my company logo. This is to indicate that my services can be done in any part of the world.

```html
<!DOCTYPE html>
<html lang="en">
<head>
<meta charset="utf-8">
<title>Velmora Buildworks – Business Card</title>
<link href="https://fonts.googleapis.com/css2?family=Jost:wght@400;500;600&family=Roboto:wght@400;500&display=swap" rel="stylesheet">
<style>
  :root {
    --stage: #4a4a4c;
    --card-dark: #111112;
    --card-dark-edge: #1d1d1f;
    --card-light: #ffffff;
    --brand-red: #e0212b;
    --wordmark-grey: #6d6d6f;
    --ink: #111111;
    --services-text: #c9c9c9;
  }
  * { box-sizing: border-box; margin: 0; padding: 0; }
  html, body {
    width: 1200px; height: 1000px; overflow: hidden;
    background: var(--stage);
    font-family: "Jost", "Helvetica Neue", Arial, sans-serif;
  }
  .canvas {
    position: relative; width: 1200px; height: 1000px;
    display: flex; flex-direction: column; align-items: center; justify-content: center; gap: 50px;
  }
  .card {
    position: relative; width: 700px; height: 400px;
    border-radius: 22px; overflow: hidden;
    box-shadow: 0 14px 30px rgba(0,0,0,0.35);
  }

  /* Back side */
  .card--back { background: radial-gradient(ellipse at 50% 40%, var(--card-dark-edge), var(--card-dark) 70%); }
  .world-map {
    position: absolute; left: 40px; top: 20px; width: 620px; height: 300px;
    background: radial-gradient(ellipse at 50% 45%, rgba(90,90,95,0.35), rgba(40,40,42,0.15) 60%, transparent 80%);
    border-radius: 40%;
  }
  .back-wordmark {
    position: absolute; left: 0; right: 0; top: 120px; text-align: center;
    font-weight: 500; font-size: 34px; letter-spacing: 3px; color: var(--wordmark-grey);
    text-transform: uppercase;
  }
  .services {
    position: absolute; left: 50px; right: 50px; top: 215px; text-align: center;
    color: var(--services-text); font-size: 15px; line-height: 1.35;
  }
  .services__title { color: var(--brand-red); font-size: 16px; font-weight: 500; margin-bottom: 6px; letter-spacing: 0.5px; }

  /* Front side */
  .card--front { background: var(--card-light); }
  .front-wordmark {
    position: absolute; left: 0; right: 0; top: 95px; text-align: center;
    font-weight: 500; font-size: 36px; letter-spacing: 3px; color: var(--wordmark-grey);
    text-transform: uppercase;
  }
  .holder {
    position: absolute; right: 380px; top: 205px; text-align: right;
    font-family: "Roboto", Arial, sans-serif;
  }
  .holder__name { color: var(--brand-red); font-size: 24px; font-weight: 500; }
  .holder__title { color: var(--ink); font-size: 15px; margin-top: 3px; }
  .divider { position: absolute; left: 340px; top: 200px; width: 2px; height: 132px; background: var(--brand-red); }
  .contacts {
    position: absolute; left: 358px; top: 198px;
    font-size: 17px; line-height: 1.2; color: var(--ink); font-weight: 500;
  }
  .contacts__label { color: var(--brand-red); font-weight: 400; font-size: 16px; }
  .contacts__row { display: flex; align-items: center; gap: 7px; }
  .contacts__row svg { width: 14px; height: 14px; flex: none; }
  .accent { color: var(--brand-red); }
  .red-band { position: absolute; left: 0; right: 0; bottom: 0; height: 22px; background: var(--brand-red); }
</style>
</head>
<body>
<main class="canvas">
  <section class="card card--back" aria-label="Card back">
    <div class="world-map" role="img" aria-label="Faint world map with connecting network lines"></div>
    <div class="back-wordmark">Velmora Buildworks</div>
    <div class="services">
      <p class="services__title">OUR SERVICES</p>
      <p>Exhibition Booth Fabrication | Outdoor Booth Setup | Interior Design | Installation and Dismantle | Exhibition Management | Shell Scheme Display Booth | Custom Stand Design | Exhibition Furniture and Equipment | Exhibition Project Management</p>
    </div>
  </section>

  <section class="card card--front" aria-label="Card front">
    <div class="front-wordmark">Velmora Buildworks</div>
    <div class="holder">
      <p class="holder__name">Marcus Lindqvist</p>
      <p class="holder__title">President</p>
    </div>
    <div class="divider"></div>
    <div class="contacts">
      <p class="contacts__label">Singapore Contact:</p>
      <p>+65 9184 2207</p>
      <p class="contacts__label">Qatar Contact:</p>
      <p>+974 7046 1938</p>
      <p class="contacts__row">
        <svg viewBox="0 0 16 16" aria-hidden="true"><rect x="1" y="3" width="14" height="10" rx="1.5" fill="var(--brand-red)"/><path d="M1.5 4 8 9l6.5-5" stroke="#fff" stroke-width="1.4" fill="none"/></svg>
        info@velmora-buildworks.com
      </p>
      <p class="contacts__row">
        <svg viewBox="0 0 16 16" aria-hidden="true"><circle cx="8" cy="8" r="7" fill="var(--brand-red)"/><path d="M1 8h14M8 1c-3 3.5-3 10.5 0 14M8 1c3 3.5 3 10.5 0 14" stroke="#fff" stroke-width="1" fill="none"/></svg>
        <span>www.<span class="accent">velmora-buildworks</span>.com</span>
      </p>
    </div>
    <div class="red-band"></div>
  </section>
</main>
</body>
</html>
```